Interior Stylist business card design needed

I need a business card for my new company in Sydney called "Liv Harrowby Designs". The business offers an interior styling and colour consultancy. My clients are generally not very design savvy (hence why they use me) and can range from being quite conservative to really wanting something "out there". They can be looking for a budget makeover or something more expensive / substantial. I'd like my business card design to be stylish (but not overly formal). I certainly don't want it to be conservative. I'd like it to stand out a bit! I don't really have any aversion to particular colours and I don't have a logo as such - my business name is really all I have.

Target Market(s)

As above - home owners, ranging from conservative to modern

Industry/Entity Type

Conservative

Contact Information for Business Card

Liv Harrowby Designs
Colour consultancy and interior styling
ph: 0417 238 605
email: livharrowby@qoralnet.net.au

Requirements
Should not have
• Old fashioned writing or motifs. No Times Roman font!!

```html
<!DOCTYPE html>
<html lang="en">
<head>
<meta charset="utf-8">
<title>Liv Harrowby Designs — Business Card</title>
<link rel="stylesheet" href="https://fonts.googleapis.com/css2?family=Open+Sans:wdth,wght@75..100,300..700&display=swap">
<style>
  :root {
    --card-grey: #e2e3e5;
    --edge-white: #ffffff;
    --ink: #0d0d0d;
    --ink-soft: #1e1e1e;
    --paint-yellow: #ecc535;
    --paint-amber: #f0c328;
    --paint-orange: #e9744f;
    --paint-red: #e9532e;
    --paint-sky: #5fc4ea;
    --paint-blue: #35b6e6;
    --paint-ocean: #3aa7dc;
    --paint-indigo: #6f88c6;
  }
  * { margin: 0; padding: 0; box-sizing: border-box; }
  html, body {
    width: 1200px;
    height: 649px;
    overflow: hidden;
    background: var(--edge-white);
  }
  .card {
    position: relative;
    width: 1200px;
    height: 649px;
    overflow: hidden;
    background: var(--edge-white);
    font-family: "Open Sans", Arial, sans-serif;
    color: var(--ink);
  }
  .card__face {
    position: absolute;
    left: 0;
    top: 0;
    width: 1136px;
    height: 649px;
    background: var(--card-grey);
  }
  .identity {
    position: absolute;
    left: 44px;
    top: 206px;
    width: 600px;
    text-align: center;
  }
  .identity__name {
    font-weight: 700;
    font-size: 47px;
    line-height: 1;
    letter-spacing: 0.2px;
  }
  .identity__services {
    position: absolute;
    left: 51px;
    top: 271px;
    width: 600px;
    text-align: center;
    font-weight: 300;
    font-stretch: 75%;
    font-size: 29px;
    line-height: 1;
    color: var(--ink-soft);
  }
  .contact {
    position: absolute;
    left: 51px;
    width: 600px;
    text-align: center;
    font-weight: 300;
    font-size: 28px;
    line-height: 1;
    color: var(--ink-soft);
    font-style: normal;
  }
  .contact--phone { top: 394px; }
  .contact--email { top: 468px; }
  .paint-swatches {
    position: absolute;
    left: 668px;
    top: 35px;
    width: 468px;
    height: 569px;
  }
</style>
</head>
<body>
  <div class="card">
    <div class="card__face"></div>

    <div class="identity">
      <h1 class="identity__name">Liv Harrowby Designs</h1>
    </div>
    <p class="identity__services">Colour Consultancy &amp; Interior Styling</p>

    <address class="contact contact--phone">0417 238 605</address>
    <address class="contact contact--email">livharrowby@qoralnet.net.au</address>

    <svg class="paint-swatches" viewBox="0 0 468 569" role="img" aria-label="Painted brush-stroke colour swatches in yellow, orange-red and blue bands">
      <defs>
        <linearGradient id="swatchBands" x1="0" y1="0" x2="0" y2="1">
          <stop offset="0" stop-color="var(--paint-yellow)"/>
          <stop offset="0.3" stop-color="var(--paint-amber)"/>
          <stop offset="0.36" stop-color="var(--paint-orange)"/>
          <stop offset="0.5" stop-color="var(--paint-red)"/>
          <stop offset="0.6" stop-color="var(--paint-orange)"/>
          <stop offset="0.66" stop-color="var(--paint-sky)"/>
          <stop offset="0.78" stop-color="var(--paint-blue)"/>
          <stop offset="0.88" stop-color="var(--paint-ocean)"/>
          <stop offset="1" stop-color="var(--paint-indigo)"/>
        </linearGradient>
      </defs>
      <rect x="0" y="0" width="468" height="569" fill="url(#swatchBands)"/>
    </svg>
  </div>
</body>
</html>
```